Catering Menu Package

I currently have a complete menu package, which we have redesigned as far as content, now I need to it put together in a catalog type format. It is essentially 10-12 pages in length, and will be sent for print production. Upon receiving a final edit
Updates

I have added an example gif to the project.

I did this free hand this basically what I am looking for. please change text and type to whatever you think would look best. This is a total rough design so, feel free to change any and everything. The text for the page is on the word documents. If you need more images let me know I am in the process of getting as many images uploaded for your use.

Project Deadline Extended
Reason: I figured we got a late jump with questions, so i am extending a few days .

Target Market(s)

The target market is business who wish to have catered luncheons, breakfasts , meetings

Industry/Entity Type

Catering

Requirements
Must have
• I have attached a copy of the text that what we want in the package, our logo, and i have also attached a catering package of another company to give you an idea what the finished product will be
Should not have
• It should not look identical to the example catering packages, these are for some inspiration we want our own design with the same type of look and feel

```html
<!DOCTYPE html>
<html lang="en">
<head>
<meta charset="utf-8">
<title>Breakfast Menu – Hartwell Field Caterers</title>
<link rel="stylesheet" href="https://fonts.googleapis.com/css2?family=Pinyon+Script&family=Amaranth&display=swap">
<style>
  :root {
    --paper: #ede7dc;
    --paper-tone: #e4ddd0;
    --ink: #1d1a17;
    --photo-red: #b3231c;
    --photo-gold: #d9b64a;
    --photo-cream: #efe3a8;
    --photo-deep: #5a1410;
    --brand-light: #f4efe2;
  }
  * { margin: 0; padding: 0; box-sizing: border-box; }
  html, body { width: 1200px; height: 928px; overflow: hidden; background: var(--paper); }
  .menu-page {
    position: relative;
    width: 1200px;
    height: 928px;
    display: flex;
  }
  .menu-panel {
    width: 696px;
    height: 100%;
    background: radial-gradient(circle at 40% 50%, var(--paper) 0%, var(--paper-tone) 100%);
    padding-right: 28px;
    text-align: right;
    color: var(--ink);
  }
  .section-title {
    font-family: "Pinyon Script", cursive;
    font-weight: 400;
    font-size: 40px;
    line-height: 1;
    margin-bottom: 8px;
  }
  .menu-section.breakfast-items { padding-top: 194px; }
  .menu-section.beverages { padding-top: 106px; }
  .item-list { list-style: none; }
  .item-list li {
    font-family: "Amaranth", sans-serif;
    font-size: 17px;
    line-height: 21px;
  }
  .photo-panel {
    position: relative;
    width: 504px;
    height: 100%;
    background:
      radial-gradient(ellipse at 70% 68%, var(--photo-cream) 0%, var(--photo-gold) 35%, transparent 60%),
      linear-gradient(160deg, var(--photo-red) 0%, var(--photo-red) 30%, var(--photo-deep) 75%, var(--photo-red) 100%);
  }
  .brand-mark {
    position: absolute;
    right: 42px;
    bottom: 40px;
    display: flex;
    flex-direction: column;
    align-items: center;
    gap: 8px;
    width: 92px;
  }
  .brand-mark svg { display: block; }
  .brand-name {
    font-family: "Amaranth", sans-serif;
    font-size: 14px;
    line-height: 16px;
    color: var(--brand-light);
    text-align: center;
  }
</style>
</head>
<body>
<main class="menu-page">
  <section class="menu-panel">
    <div class="menu-section breakfast-items">
      <h2 class="section-title">Ala Carte Breakfast Items</h2>
      <ul class="item-list">
        <li>Buttermilk Pancakes</li>
        <li>served with Warm Maple Syrup and Whipped Butter</li>
        <li>Redskin Potato Hash Browns</li>
        <li>Maple Sausage Links</li>
        <li>Applewood Smoked Bacon</li>
        <li>Turkey Bacon</li>
        <li>Country Ham</li>
        <li>Fresh Fruit Platter</li>
        <li>Whole Fruit Basket</li>
      </ul>
    </div>
    <div class="menu-section beverages">
      <h2 class="section-title">Breakfast Beverages</h2>
      <ul class="item-list">
        <li>Fresh Squeezed Orange Juice</li>
        <li>Cranberry Juice</li>
        <li>Apple Juice</li>
        <li>Bottled Water</li>
        <li>Bottled Juices</li>
        <li>Brennholt Select Gourmet Coffee Station</li>
        <li>Hot Tea</li>
      </ul>
    </div>
  </section>
  <section class="photo-panel" role="img" aria-label="Plated breakfast dish with asparagus and potatoes on a red checkered tablecloth beside a fork and a printed card">
    <div class="brand-mark">
      <svg width="60" height="60" viewBox="0 0 60 60" aria-hidden="true">
        <circle cx="30" cy="30" r="28" fill="var(--brand-light)"/>
      </svg>
      <span class="brand-name">Hartwell Field Caterers</span>
    </div>
  </section>
</main>
</body>
</html>
```